Website for Ashcombe Tube Drift

Require a website for a river float in the City of Larkfield. Located on Ashcombe River River. Will need to be a coded website with incorporated booking system through Fare Harbor software.

Pages include
Home
Pricing
About
FAQ
Contact

Ashcombe Tube Drift is an activity based business that will have customers floating down the Ashcombe River river in Larkfield AB. The site will have all information needed and a full reservation system. The project was launched to provide people in the Larkfield area a favorite summer activity.

Here are similar websites to reference what our business will be doing and what we are looking for.

mossbankfloatco.com
quillpointpaddles.com

Target Market(s)

Families, Groups, Individuals, Anyone who wants to explore the river

Industry/Entity Type

Activities based business/ Outdoor recreational/ River Float

Coding

Coded - Design and coding required

Number of Pages Required

5+ page

Colors
0054AA
0677BA
7BADD7
CADEEF
E8F1F8
F0912C
F2A743
F7CA91
FBE8D2
FDF5EE

```html
<!DOCTYPE html>
<html lang="en">
<head>
<meta charset="utf-8">
<title>Ashcombe Tube Drift</title>
<link href="https://fonts.googleapis.com/css2?family=Poppins:wght@300;400;500;600&display=swap" rel="stylesheet">
<style>
:root{
  --navy:#0b2e66;
  --cyan:#4ec6e8;
  --cyan-shadow:#0b2e66;
  --ink:#1d1d1d;
  --mist:#f4f8fc;
  --sky-top:#9fb7e8;
  --sky-mid:#f1e7dc;
  --green:#5f8a3a;
  --water:#6f8a8c;
  --white:#ffffff;
  --footer-text:#ffffff;
}
*{margin:0;padding:0;box-sizing:border-box}
html,body{width:1200px;height:2488px;overflow:hidden}
body{position:relative;font-family:"Poppins",sans-serif;background:var(--white);color:var(--navy)}
.abs{position:absolute}

.site-header{position:absolute;left:0;top:0;width:1200px;height:104px;background:var(--white);z-index:3}
.brand-box{position:absolute;left:86px;top:0;width:208px;height:175px;background:var(--white);z-index:4;display:flex;flex-direction:column;align-items:center;justify-content:center;gap:12px}
.brand-dot{width:70px;height:70px;border-radius:50%;background:var(--cyan)}
.brand-name{font-weight:600;font-size:17px;color:var(--navy);text-align:center;line-height:1.2;white-space:nowrap}
.main-nav{position:absolute;right:88px;top:40px;display:flex;gap:28px;font-size:15px;font-weight:500;color:var(--ink)}
.main-nav .active{color:var(--cyan)}

.hero{position:absolute;left:0;top:104px;width:1200px;height:690px;overflow:hidden}
.hero-photo{position:absolute;inset:0;background:linear-gradient(180deg,var(--sky-top) 0%,#dcd9e4 25%,var(--sky-mid) 42%,#b9b2a4 55%,var(--green) 68%,var(--water) 82%,#a7c8a0 100%)}
.hero-title{position:absolute;left:0;top:104px;width:1200px;text-align:center;font-size:57px;font-weight:400;letter-spacing:1px;color:transparent;-webkit-text-stroke:1.6px var(--navy)}
.hero-sub{position:absolute;left:0;top:185px;width:1200px;text-align:center;font-size:16px;color:var(--ink)}

.btn{position:absolute;height:58px;border-radius:30px;background:var(--cyan);color:var(--white);font-size:21px;font-weight:400;display:flex;align-items:center;justify-content:center;box-shadow:4px 4px 0 var(--cyan-shadow)}

.feature-photo{position:absolute;border-radius:50%;border:14px solid var(--navy)}
.photo-vans{left:87px;top:871px;width:454px;height:454px;background:radial-gradient(circle at 40% 60%,#d8d8d8,#8a8a8a 70%,#5d6a4c)}
.photo-tube{left:359px;top:1102px;width:228px;height:228px;background:linear-gradient(180deg,#8fa765 0%,#b18cc8 35%,#6ea0b8 60%,#3e78a8 100%);border-width:12px;box-shadow:0 0 0 8px var(--white)}
.section-title{position:absolute;font-size:36px;font-weight:600;line-height:45px;color:var(--navy)}
.section-text{position:absolute;font-size:15px;line-height:24.6px;color:var(--navy)}
.deco-circle{position:absolute;left:1000px;top:1265px;width:240px;height:240px;border-radius:50%;background:var(--cyan);opacity:.9}

.mist-band{position:absolute;left:0;top:1400px;width:1200px;height:656px}
.photo-frame{position:absolute;left:627px;top:1534px;width:486px;height:407px;background:var(--cyan);border-radius:40px}
.photo-kayak{position:absolute;left:592px;top:1545px;width:508px;height:410px;border-radius:40px;background:linear-gradient(180deg,#e9e4d2 0%,#c4b494 35%,#e8843a 60%,#c9473c 80%,#7e8f9a 100%)}

.site-footer{position:absolute;left:0;top:2056px;width:1200px;height:432px;background:var(--navy);color:var(--footer-text)}
.foot-col{position:absolute;text-align:center}
.foot-head{font-size:20px;font-weight:500}
.foot-rule{width:30px;height:2px;background:var(--white);margin:10px auto 0}
.contact-list{font-size:16px;line-height:28px;margin-top:20px}
.contact-list b{font-weight:500}
.social{display:flex;gap:12px;justify-content:center;margin-top:20px}
.social span{width:44px;height:44px;border-radius:5px;background:rgba(255,255,255,.12)}
.mail-note{margin-top:18px;font-size:16px}
.mail-note a{color:var(--cyan);font-weight:600;text-decoration:none}
.foot-brand{left:430px;top:84px;width:340px;display:flex;flex-direction:column;align-items:center}
.foot-dot{width:120px;height:120px;border-radius:50%;background:var(--cyan)}
.foot-name{font-size:22px;font-weight:600;margin-top:14px;white-space:nowrap}
.foot-tag{font-size:16px;margin-top:8px}
.foot-links{list-style:none;font-size:16px;line-height:38.6px;margin-top:20px}
.foot-divider{position:absolute;left:86px;top:365px;width:1028px;height:1px;background:rgba(255,255,255,.35)}
.copyright{position:absolute;left:0;top:380px;width:1200px;text-align:center;font-size:16px}
</style>
</head>
<body>

<header class="site-header">
  <nav class="main-nav">
    <span class="active">HOME</span><span>PRICING</span><span>ABOUT</span><span>FAQ</span><span>CONTACT</span>
  </nav>
</header>
<div class="brand-box">
  <span class="brand-dot"></span>
  <span class="brand-name">Ashcombe Tube Drift</span>
</div>

<section class="hero">
  <div class="hero-photo" role="img" aria-label="City skyline above a river, bridge and green riverbank at sunset"></div>
  <h1 class="hero-title">ASHCOMBE TUBE DRIFT</h1>
  <p class="hero-sub">Float the Ashcombe River through downtown Larkfield</p>
  <a class="btn" style="left:510px;top:228px;width:173px">Book Now</a>
</section>
<svg class="abs" style="top:725px;left:0;width:1200px;height:90px" viewBox="0 0 1200 90" preserveAspectRatio="none">
  <path d="M0 60 C120 75 250 35 360 25 C470 15 520 55 640 45 C760 35 820 20 900 30 C1000 45 1080 10 1200 30 L1200 90 L0 90Z" fill="#cbd6e4"/>
  <path d="M0 72 C130 90 250 55 360 40 C470 30 530 65 640 50 C760 35 820 18 900 35 C1000 55 1090 18 1200 40 L1200 90 L0 90Z" fill="#ffffff"/>
</svg>

<section class="feature-shuttle">
  <div class="feature-photo photo-vans" role="img" aria-label="Row of white shuttle vans parked by trees"></div>
  <div class="feature-photo photo-tube" role="img" aria-label="People on a blue float tube on the river"></div>
  <h2 class="section-title" style="left:655px;top:958px;width:440px">Shuttle Service And Gear Included</h2>
  <p class="section-text" style="left:656px;top:1070px;width:470px">We provide everything you need including round trip shuttle service, float tube, lifejacket, paddle, and more. Fun for everyone!</p>
  <a class="btn" style="left:656px;top:1170px;width:174px">Learn More</a>
  <div class="deco-circle"></div>
</section>

<svg class="mist-band" viewBox="0 0 1200 656" preserveAspectRatio="none">
  <path d="M0 30 C120 10 200 10 280 25 C360 40 420 30 520 15 C620 0 700 30 800 35 C900 40 1000 20 1200 25 L1200 656 L0 656Z" fill="#f4f8fc"/>
</svg>

<section class="feature-floating">
  <h2 class="section-title" style="left:85px;top:1605px;width:440px">Floating 7 &amp; Days A Week</h2>
  <p class="section-text" style="left:86px;top:1716px;width:470px">Our priority is to make sure everyone has a safe and fun time on the river. Safety demonstrations are provided and staff are available to assist in any way. Whether you are a family with children, larger group or just want a relaxing way to explore the river, this is a must try activity.</p>
  <a class="btn" style="left:86px;top:1863px;width:173px">Book Now</a>
  <div class="photo-frame"></div>
  <div class="photo-kayak" role="img" aria-label="Group of friends in life jackets paddling a red kayak"></div>
</section>

<footer class="site-footer">
  <div class="foot-col" style="left:47px;top:78px;width:400px">
    <div class="foot-head">Connect</div>
    <div class="foot-rule"></div>
    <div class="contact-list">
      <div><b>EMAIL:</b> info@ashcombetubedrift.com</div>
      <div><b>LOCATION:</b> Willowbend Landing</div>
    </div>
    <div class="social"><span></span><span></span><span></span></div>
    <div class="mail-note"><a>Sign up</a> for our mailing list</div>
  </div>
  <div class="foot-col foot-brand">
    <span class="foot-dot"></span>
    <span class="foot-name">Ashcombe Tube Drift</span>
    <span class="foot-tag">Floating 7 days a week</span>
  </div>
  <div class="foot-col" style="left:800px;top:78px;width:300px">
    <div class="foot-head">Main Navigation</div>
    <div class="foot-rule"></div>
    <ul class="foot-links"><li>Home</li><li>Pricing</li><li>About</li><li>FAQ</li><li>Contact</li></ul>
  </div>
  <div class="foot-divider"></div>
  <p class="copyright">Copyright 2022.Ashcombe Tube Drift.All right reserved.</p>
</footer>

</body>
</html>
```